Tolbek cards

I want a simple business card that pops.
Logo on one side.
On side two i want.
"Are you thinking about a new building on your property, or renovating an existing structure? Contact".....
Owners Name: Dale Whitacre
Owners Phone number: 610-555-0187
Address:4076 Copper Ridge RD, Ashford, OH 43190
Committed to Quality, Service, and Integrity

```html
<!DOCTYPE html>
<html lang="en">
<head>
<meta charset="utf-8">
<title>Tolbek Builders LLC — Business Cards</title>
<link href="https://fonts.googleapis.com/css2?family=Archivo:ital,wght@0,400;0,600;0,700;0,800;1,700&display=swap" rel="stylesheet">
<style>
  :root {
    --stage: #5a5a5a;
    --paper: #ffffff;
    --walnut: #3f2d1c;
    --bronze: #9f8a72;
    --bronze-deep: #7a6049;
    --ink: #5a3e28;
  }
  html, body {
    margin: 0;
    padding: 0;
    width: 1200px;
    height: 1200px;
    overflow: hidden;
    background: var(--stage);
  }
  .canvas {
    position: relative;
    width: 1200px;
    height: 1200px;
    font-family: "Archivo", Arial, sans-serif;
  }
  .card {
    position: absolute;
    width: 690px;
    height: 395px;
    display: block;
    background: var(--paper);
  }
  .card--contact { left: 266px; top: 158px; }
  .card--brand   { left: 262px; top: 652px; }
  .question { font-style: italic; font-weight: 700; font-size: 33px; fill: var(--ink); }
  .wordmark { font-weight: 800; fill: var(--walnut); }
  .owner-name { font-weight: 700; font-size: 47px; fill: var(--walnut); letter-spacing: 0.5px; }
  .contact-line { font-weight: 400; font-size: 28px; fill: var(--paper); }
  .tagline { font-weight: 400; font-size: 26.5px; fill: var(--paper); }
  .web { font-weight: 400; font-size: 25px; fill: var(--paper); letter-spacing: 5px; }
</style>
</head>
<body>
<main class="canvas">

  <!-- Contact side -->
  <svg class="card card--contact" viewBox="0 0 1108 634" preserveAspectRatio="none" aria-label="Tolbek Builders LLC contact card">
    <rect width="1108" height="634" fill="var(--paper)"/>
    <polygon class="panel-dark" points="618,357 1108,357 1108,634 361,634" fill="var(--walnut)"/>
    <polygon class="band-tagline-edge" points="0,545 560,545 548,557 0,557" fill="var(--bronze-deep)"/>
    <polygon class="band-tagline" points="0,442 663,438 560,545 0,545" fill="var(--bronze)"/>
    <polygon class="band-web" points="684,521 1108,521 1108,588 618,590" fill="var(--bronze)"/>

    <text class="question" x="1071" y="88" text-anchor="end">Are you thinking about a new building on your property,</text>
    <text class="question" x="1071" y="127" text-anchor="end">or renovating an existing structure?</text>

    <text class="wordmark" x="221" y="355" font-size="82" text-anchor="middle">TOLBEK</text>
    <text class="wordmark" x="221" y="387" font-size="28" text-anchor="middle" letter-spacing="1.5">BUILDERS LLC</text>

    <text class="owner-name" x="1071" y="323" text-anchor="end">DALE WHITACRE</text>

    <text class="contact-line" x="1036" y="413" text-anchor="end">610-555-0187</text>
    <path class="icon-phone" fill="var(--paper)" d="M1053,390 c3,-2 6,-1 7,2 l3,6 c1,2 0,4 -2,5 l-2,1 c1,4 5,9 9,11 l2,-2 c1,-2 3,-2 5,-1 l5,4 c2,2 2,4 0,6 l-3,3 c-3,3 -10,1 -16,-5 c-7,-7 -10,-17 -8,-21 z"/>
    <text class="contact-line" x="1071" y="460" text-anchor="end">4076 Copper Ridge RD</text>
    <text class="contact-line" x="1071" y="494" text-anchor="end">Ashford, OH 43190</text>

    <text class="tagline" x="50" y="500">Committed to Quality, Service, and Integrity</text>
    <text class="web" x="1071" y="560" text-anchor="end">www.TOLBEK.com</text>
  </svg>

  <!-- Brand side -->
  <svg class="card card--brand" viewBox="0 0 1114 636" preserveAspectRatio="none" aria-label="Tolbek Builders LLC brand card">
    <defs>
      <linearGradient id="bronzeSheen" x1="0" y1="0" x2="1" y2="0">
        <stop offset="0" stop-color="#7a6049"/>
        <stop offset="0.5" stop-color="#9f8a72"/>
        <stop offset="1" stop-color="#7a6049"/>
      </linearGradient>
      <linearGradient id="barFade" x1="0" y1="0" x2="1" y2="0">
        <stop offset="0.1" stop-color="#ffffff"/>
        <stop offset="0.3" stop-color="#937b63"/>
        <stop offset="0.65" stop-color="#9f8a72"/>
        <stop offset="1" stop-color="#7a6049"/>
      </linearGradient>
    </defs>
    <rect width="1114" height="636" fill="var(--paper)"/>
    <polygon class="stripe-sheen" points="0,0 176,0 0,370" fill="url(#bronzeSheen)"/>
    <polygon class="panel-dark" points="176,0 501,0 206,636 0,636 0,370" fill="var(--walnut)"/>
    <polygon class="bar-accent" points="186,513 1114,513 1114,589 144,589" fill="url(#barFade)"/>

    <rect class="brand-square" x="470" y="262" width="112" height="112" fill="var(--walnut)"/>
    <text class="wordmark" x="641" y="356" font-size="92">TOLBEK</text>
    <text class="wordmark" x="643" y="390" font-size="30" letter-spacing="1.5">BUILDERS LLC</text>
    <rect class="edge-block" x="1091" y="281" width="23" height="90" fill="var(--walnut)"/>
  </svg>

</main>
</body>
</html>
```